Car rental website design for a UAE car rental company

This project is about creating a new website design for a car rental company located in Dubai (United Arab Emirates), I opened the same project a few months ago but I didn't receive a lot of appealing entries so I closed it but this time I am marking the project as guaranteed to avoid such situation again, if you have already provided a design before then please re-submit again on this project so that it is considered while reviewing all the designs

A few important things:

1- We need a simple non-complex design
2- The final deliverable would be 2 screens (PSD, JPEG ... etc), the first screen is for the home page and the second screen is for an internal page
3- The home page must have a section that end users can use to rent a car online directly from the home page instead of going into some inner pages
4- The current website is very old and not very appealing so avoid creating a similar design (www.crestvane-autos.example)
5- The name is Crestvane but the company rents normal cars (no Limousin cars will be rented) so avoid adding any fancy cars in the images/graphics used in the design, just normal end users cars
6- The expected pages would be: home, About us, Our team, Strategy, Contact us and links to social media pages
7- The attachments include the company's logo and some screens from other car rental companies that provide online rentals/payments

If you have any questions please feel free to ask and please note that we will need the designs urgently

Thanks

Target Market(s)

Dubai - United Arab Emirates

Industry/Entity Type

It Company

Number of Pages Required

2 page

Font styles to use
Sans Serif

Requirements
Must have
• Check the project details
Nice to have
Should not have

```html
<!DOCTYPE html>
<html lang="en">
<head>
<meta charset="utf-8">
<title>Crestvane Rent A Car</title>
<link rel="stylesheet" href="https://fonts.googleapis.com/css2?family=Roboto+Slab:wght@300;400&family=Open+Sans:wght@400;600&display=swap">
<style>
:root{
  --crimson:#a5123f;
  --sage:#8a9a8e;
  --ink:#333;
  --muted:#777;
  --panel:#ecebe8;
  --light:#f3f3f3;
  --white:#fff;
}
*{box-sizing:border-box;margin:0;padding:0}
html,body{width:1121px;height:1200px;overflow:hidden;background:var(--white)}
body{position:relative;font-family:"Roboto Slab",serif;font-weight:300;color:var(--ink)}
.abs{position:absolute}
a{color:inherit;text-decoration:none}

/* header */
.site-header{left:0;top:0;width:1121px;height:98px;background:linear-gradient(#f7f7f7,#e9e9e9);border-bottom:2px solid var(--crimson)}
.brand{left:75px;top:26px;display:flex;align-items:center;gap:12px}
.brand-mark{width:44px;height:44px;border:3px solid var(--crimson)}
.brand-name{font-size:32px;font-weight:400;color:var(--crimson)}
.social{display:flex;gap:7px}
.social span{width:24px;height:24px;border-radius:50%;background:#4a6fa5}
.social span:nth-child(2){background:#3fa2d8}
.social span:nth-child(3){background:#2f77b2}
.social span:nth-child(4){background:#d34836}
.header-social{left:564px;top:17px}
.call{left:788px;top:14px;display:flex;align-items:center;gap:8px;font-size:17px;color:var(--crimson);font-weight:400}
.main-nav{left:564px;top:66px;display:flex;gap:24px;font-size:15px;color:var(--muted)}
.main-nav .active{color:var(--crimson)}

/* hero */
.hero-image{left:0;top:100px;width:1121px;height:408px;background:linear-gradient(100deg,#2b241c 0%,#6b5237 30%,#b98a50 55%,#d6a660 75%,#8a6a46 100%)}
.hero-title{left:78px;top:400px;width:560px;font-size:29px;line-height:36px;color:var(--white);font-weight:300}
.hero-line{left:0;top:506px;width:1121px;height:3px;background:var(--crimson)}
.hero-next{left:1070px;top:290px}

/* booking */
.booking{left:655px;top:98px;width:392px;height:408px;background:var(--crimson)}
.booking-tabs{left:660px;top:105px;display:flex;font-size:15px;color:var(--white)}
.tab{padding:7px 10px;height:36px}
.tab.current{background:var(--sage)}
.booking-body{left:660px;top:141px;width:383px;height:360px;background:var(--panel)}
.step{width:22px;height:22px;border:1px solid var(--crimson);background:var(--white);font-size:14px;text-align:center;line-height:20px;font-weight:400}
.lbl{font-size:13.5px;color:var(--ink);font-weight:400}
.link{font-size:13.5px;color:var(--crimson);text-decoration:underline;font-weight:400}
.field{height:26px;border:1px solid #777;background:#f3f2f0;font-size:12px;line-height:24px;padding-left:6px;font-weight:400}
.check{display:inline-block;width:9px;height:9px;border:1px solid #555;margin-right:5px}
.help{width:20px;height:20px;border-radius:50%;background:var(--sage);color:var(--white);font-size:11px;text-align:center;line-height:20px}
.spin{width:20px;height:26px;border-left:1px solid #999;font-size:9px;text-align:center;line-height:12px;color:#444}
.quote{left:908px;top:466px;width:126px;height:38px;background:var(--crimson);color:var(--white);font-size:15px;text-align:center;line-height:38px;font-weight:400}

/* features */
.features{left:0;top:509px;width:1121px;height:254px;background:var(--light);border-bottom:1px solid #ddd}
.feature{top:540px;width:240px;text-align:center}
.feature-icon{width:88px;height:88px;border-radius:50%;border:2px solid #8a9a8e;margin:0 auto 22px;display:flex;align-items:center;justify-content:center;background:var(--white)}
.feature-icon.accent{border-color:var(--crimson)}
.feature h3{font-size:15px;font-weight:400;line-height:20px;margin-bottom:8px}
.feature p{font-family:"Open Sans",sans-serif;font-size:13.5px;line-height:19px;color:#444}

/* content */
.section-title{font-size:18px;color:var(--sage);font-weight:300;padding-bottom:6px;width:436px;border-bottom:1px dashed #aaa}
.section-title em{font-style:normal;color:var(--crimson);font-weight:400}
.copy{font-size:13.5px;line-height:21px;font-weight:400;color:#222}
.divider{left:78px;top:960px;width:700px;height:2px;background:linear-gradient(90deg,transparent,#ddd,transparent)}
.car-photo{width:200px;height:100px;border-radius:40px 40px 10px 10px}
.car-silver{left:840px;top:790px;background:linear-gradient(#d9d9d9,#8c8c8c)}
.car-red{left:840px;top:993px;background:linear-gradient(#e04040,#8f1010)}
.price{width:204px;height:38px;background:var(--sage);color:var(--white);font-size:15px;font-weight:400;text-align:center;line-height:38px}

/* footer */
.site-footer{left:0;top:1146px;width:1121px;height:54px;background:var(--crimson);color:var(--white)}
.footer-nav{left:76px;top:18px;display:flex;gap:18px;font-size:13.5px;font-weight:400}
.footer-social{left:623px;top:15px}
.footer-social span{border:2px solid var(--white)}
.legal{left:813px;top:18px;font-family:"Open Sans",sans-serif;font-size:13px}
</style>
</head>
<body>

<header class="abs site-header">
  <div class="abs brand"><span class="brand-mark"></span><span class="brand-name">Crestvane</span></div>
  <div class="abs social header-social"><span></span><span></span><span></span><span></span></div>
  <div class="abs call">
    <svg width="34" height="40" viewBox="0 0 34 40"><path d="M6 20a11 11 0 0 1 22 0" fill="none" stroke="#555" stroke-width="3"/><rect x="3" y="18" width="7" height="12" rx="3" fill="var(--crimson)"/><rect x="24" y="18" width="7" height="12" rx="3" fill="var(--crimson)"/><path d="M27 30q0 6-8 6" fill="none" stroke="#555" stroke-width="2"/></svg>
    Call us at +971 4 555 0182
  </div>
  <nav class="abs main-nav"><a class="active">HOME</a><a>ABOUT US</a><a>OUR TEAM</a><a>STRATEGY</a><a>CONTACT US</a></nav>
</header>

<div class="abs hero-image" role="img" aria-label="Bronze SUV driving on an evening road with a city skyline at sunset"></div>
<div class="abs hero-title">Experience An Extra Mile of comfort, pleasure and leisure From the best</div>
<svg class="abs hero-next" width="14" height="24" viewBox="0 0 14 24"><path d="M2 2l10 10-10 10" fill="none" stroke="#fff" stroke-width="2"/></svg>
<div class="abs hero-line"></div>

<section class="abs booking"></section>
<div class="abs booking-tabs"><span class="tab current">Book A Car</span><span class="tab">View / Modify / Cancel A Reservation</span></div>
<div class="abs booking-body"></div>
<div class="abs step" style="left:665px;top:152px">1</div>
<div class="abs lbl" style="left:704px;top:152px">Pick-up Location &nbsp;(City, State or Airport Code</div>
<div class="abs link" style="left:704px;top:173px">Previous Searches</div>
<div class="abs field" style="left:704px;top:197px;width:317px">Dubai Airport - Terminal 3</div>
<div class="abs link" style="left:704px;top:229px">Help me find a rental location</div>
<div class="abs lbl" style="left:704px;top:254px"><span class="check"></span>Return car to a different Roverline Location</div>
<div class="abs help" style="left:981px;top:251px">?</div>
<div class="abs step" style="left:665px;top:286px">2</div>
<div class="abs lbl" style="left:704px;top:286px">Pick-up Date &amp; Time</div>
<div class="abs field" style="left:704px;top:309px;width:156px">26/03/2015</div>
<div class="abs field" style="left:864px;top:309px;width:156px">16:00</div>
<div class="abs spin" style="left:1000px;top:309px">^<br>v</div>
<div class="abs lbl" style="left:704px;top:345px">Return Date &amp; Time</div>
<div class="abs field" style="left:704px;top:368px;width:156px">26/03/2015</div>
<div class="abs field" style="left:864px;top:368px;width:156px">16:00</div>
<div class="abs spin" style="left:1000px;top:368px">^<br>v</div>
<div class="abs lbl" style="left:704px;top:405px">Hire Car Type</div>
<div class="abs field" style="left:704px;top:428px;width:156px">Automatic</div>
<div class="abs lbl" style="left:868px;top:431px;font-size:12.5px"><span class="check"></span>Apply a discount Code</div>
<div class="abs help" style="left:1018px;top:428px">?</div>
<div class="abs quote">Get A Quote</div>

<section class="abs features"></section>
<div class="abs feature" style="left:68px">
  <div class="feature-icon accent"><svg width="54" height="40" viewBox="0 0 54 40"><path d="M4 24l4-10h20l4 10v8H4z" fill="var(--crimson)"/><path d="M22 30l4-9h20l4 9v8H22z" fill="var(--crimson)" stroke="#fff" stroke-width="2"/></svg></div>
  <h3>Wide Range Of Vehicles For City Driving or SUV’s For Trips</h3>
  <p>Lorem ipsum dolor sit aonsectetuer adipiscing elied diam nonummy</p>
</div>
<div class="abs feature" style="left:331px">
  <div class="feature-icon"><svg width="40" height="40" viewBox="0 0 40 40"><path d="M8 18l12-12h12v12L20 30z" fill="#8a9a8e" transform="rotate(45 20 20)"/><circle cx="17" cy="20" r="2" fill="#fff"/><circle cx="23" cy="24" r="2" fill="#fff"/></svg></div>
  <h3>Special 10% Discount For New Customers On The First Rent</h3>
  <p>Lorem ipsum dolor sit aonsectetuer adipiscing elied diam nonummy</p>
</div>
<div class="abs feature" style="left:582px">
  <div class="feature-icon"><svg width="44" height="44" viewBox="0 0 44 44"><circle cx="16" cy="8" r="5" fill="#8a9a8e"/><rect x="20" y="6" width="14" height="4" fill="#8a9a8e"/><path d="M6 32l5-11h22l5 11v8H6z" fill="#8a9a8e"/></svg></div>
  <h3>Long Term Car<br>Rentals</h3>
  <p>Lorem ipsum dolor sit aonsectetuer adipiscing elied diam nonummy</p>
</div>
<div class="abs feature" style="left:832px">
  <div class="feature-icon"><svg width="40" height="40" viewBox="0 0 40 40"><path d="M14 8L4 17l10 9v-6q14 0 14 12 6-18-14-18z" fill="#8a9a8e"/></svg></div>
  <h3>Buyback Option After<br>Lease Term</h3>
  <p>Lorem ipsum dolor sit aonsectetuer adipiscing elied diam nonummy</p>
</div>

<h2 class="abs section-title" style="left:78px;top:792px">Welcome to Crestvane <em>Rent A Car</em></h2>
<p class="abs copy" style="left:78px;top:826px;width:700px">As Dubai is expected to welcome millions of tourists and visitors, car rental industry is believed to escalate more rapidly in the region. Over the past five years, demands for car rentals in Dubai has been augmenting at a healthy pace and is currently registering a growth rate of 20 to 25 percent per year. The swift economic growth and the number. Crestvane was established to bring comfort and pleasure to all its clients. ...</p>
<a class="abs copy" style="left:78px;top:914px;font-size:14px">Read More</a>
<div class="abs divider"></div>
<h2 class="abs section-title" style="left:78px;top:1000px">Our <em>Mission</em></h2>
<p class="abs copy" style="left:78px;top:1043px;width:700px">To be one of the leading auto leasing company in the fast growing economy and tourism industry of the emirate of Dubai &amp; play alongside with the major car rental companies in the globe.</p>
<p class="abs copy" style="left:78px;top:1088px;width:700px;line-height:19px">Crestvane vows to deliver comfort, luxury &amp; satisfaction to all our clients by providing them professional, hassle-free and first class service.</p>

<div class="abs car-photo car-silver" role="img" aria-label="Silver sedan"></div>
<div class="abs price" style="left:833px;top:888px">From Only AED 1100 p/m</div>
<div class="abs car-photo car-red" role="img" aria-label="Red sedan"></div>
<div class="abs price" style="left:837px;top:1088px">From Only AED 1100 p/m</div>

<footer class="abs site-footer">
  <nav class="abs footer-nav"><a>HOME</a><a>ABOUT US</a><a>OUR TEAM</a><a>STRATEGY</a><a>CONTACT US</a></nav>
  <div class="abs social footer-social"><span></span><span></span><span></span><span></span></div>
  <div class="abs legal">© 2015 Crestvane. All Rights Reserved</div>
</footer>

</body>
</html>
```